Superfoods Nutrition for Elderly

We need a thematic packaging design that fits our elderly nutrition products, that is based on our "3 Ws ethos" - eating Wisely, Widely & Wholly.

Wisely - selected superfoods and ingredients - NZ and other sources
Widely - based on the "rainbow diet" philosophy
Wholly - all natural, (no artificial flavours, colors etc). Formulated as complete meals (NOT supplementation)

Mediums:
- 400-450gram re-sealable doy packs
- 400-450gram re-sealable tin cans

Look n Feel:
Tuarango - https://tuarangokindness.com
Poli Vane - https://www.polvane.co.nz/
Juniper bluff - https://dinegladstaygood.co.nz/collections/cereals

The name of our products may/may not be “vital rori”. Our on-going research tells us that for the Asian market, an icon or character to personify our product may be a sound strategy. This is only for the designer to take note off.

Deliverables:
* 5 packaging designs in the range.
1x yellow + orange colored foods (star ingredient: “bright so” – passion fruit powder)
1x red colored foods (star ingredient: (star ingredient: - Manuka honey )
1x blues/purple colored foods: (star ingredient: lumoka blackcurrant)
1 x green coloured foods (star ingredient: Green kiwi)
1 x brown/white (star ingredients: harrowby’s grass fed bone broth)

brand name, please use “VitalRori” for now.

These will be the products:

Blue/purple: “Instant oatmeal porridge”
Ingredients: Rolled Baby Oats, Blueberries, Blackcurrant Powder, chia seeds, Blue Spirulina, Sheep’s Milk.
Star ingredient: Blackcurrant powder (support eyesight)

Brown/White: “Instant Brown Rice”
Ingredients: Organic Brown Rice, Grass fed bone broth powder, collagen peptide powder, black sesame seeds, onions and garlic powder, dried mushrooms, probiotics.
Star ingredient: Grass fed bone broth (support joint health)

Green: “Instant Smoothie”
Ingredients: Organic Green Kiwifruit, Kale powder, green apple powder, whey protein concentrate, probiotics, and sheep’s milk powder
Star ingredient: Organic green kiwi fruit(supports immunity)

Yellow/Orange “Instant Oatmeal”
Ingredients: Organic rolled baby oats, banana, organic passionfruit, apricot, dried mango, probiotics, cinnamon, sheep’s milk powder.
Star ingredient: Organic passionfruit(regulates blood glucose)

Red: “ instant amaranth cereal”
Ingredients: Organic amaranth, red apples, pomegranate, cranberries, Manuka honey powder, probiotics, sheep’s milk
Star ingredient: Manuka honey powder (anti-inflammatory)

Target Market(s)

Whose attention we are trying to grab?

Primary:
- 20 to 40 year olds buying these products for their parents/grand parents
- Health Nutrition conscious “golden agers”
Secondary
- Professional Caregivers to the elderly (homes, private hospitals etc)
- 40 year olds in the “prevention” mind set.

Font styles to use
Serif
Sans Serif

Colors

Designer to choose colors to be used in the design.

Requirements
Must have
• Mandatory:
• - clear visual que of the food color/s
• - "New Zealand" origin must come through strongly.
• - must have a blurp or feature of the star ingredient for each with mention of brand.
• e.g. for the blues+ purple, NZ blackcurrant powder for improved eyesight (cataract prevention).
• - icons for “heart health, “eyesight”, “mobility”, “gut-health”.
• - every other ingredient must be stated.
• The name of product may/may not be “vitalrori”. Our on-going research tells us that for the Asian market, an icon or character to personify our product may be a sound strategy. This is only for the designer to take note off.
Nice to have
• Desirables:
• Ingredient origin story - e.g blackcurrant comes from Timaru etc.
• (refer to Pemberlys destination marketing…)

```html
<!DOCTYPE html>
<html lang="en">
<head>
<meta charset="utf-8">
<title>VitalRori Instant Oatmeal – Pack Front</title>
<link rel="stylesheet" href="https://fonts.googleapis.com/css2?family=Quicksand:wght@500;600;700&display=swap">
<style>
  :root {
    --paper: #ffffff;
    --backdrop: #f1f1f1;
    --ink: #1e1e1e;
    --orange: #e8641e;
    --orange-soft: #f3a06a;
    --rule: #ef8a4e;
    --icon-grey: #a4a4a4;
    --label-grey: #9a9a9a;
    --bowl-rim: #f4f4f4;
    --bowl-cream: #ece5da;
    --bowl-oat: #d9c9b0;
    --fruit-purple: #8a2f4a;
    --fruit-pink: #d98aa0;
    --fruit-yellow: #e3b53a;
  }
  * { margin: 0; padding: 0; box-sizing: border-box; }
  html, body {
    width: 1200px; height: 1200px; overflow: hidden;
    background: var(--backdrop);
    font-family: "Quicksand", sans-serif;
  }
  .pack-front {
    position: absolute; left: 150px; top: 20px;
    width: 900px; height: 1170px;
    background: var(--paper);
    border-radius: 18px;
    overflow: hidden;
  }
  /* every block is centred on the canvas x = 600 (pack x = 450) */
  .centred {
    position: absolute; left: 450px;
    transform: translate(-50%, -50%);
    white-space: nowrap; text-align: center; line-height: 1;
  }
  .brand { top: 155px; font-weight: 700; font-size: 110px; letter-spacing: -2px; color: var(--ink); }
  .rule { position: absolute; left: 450px; transform: translateX(-50%); height: 2px; background: var(--rule); }
  .rule--top { top: 248px; width: 442px; }
  .rule--mid { top: 366px; width: 442px; }
  .product-name { top: 310px; font-weight: 600; font-size: 80px; letter-spacing: -1px; color: var(--orange); }
  .made-with { top: 406px; font-weight: 600; font-size: 24px; color: var(--orange); }
  .star-ingredient { top: 446px; font-weight: 600; font-size: 39px; color: var(--orange); }
  .benefit-pill {
    top: 491px; padding: 4px 16px;
    background: var(--orange); color: #fff;
    border-radius: 10px; font-weight: 600; font-size: 22px;
  }
  .hero-visual { position: absolute; left: 170px; top: 560px; width: 580px; height: 380px; }
  .hero-visual .fruit-left {
    position: absolute; left: 7px; top: 10px; width: 195px; height: 202px; border-radius: 50%;
    background: radial-gradient(circle at 35% 65%, var(--fruit-yellow) 0 26%, var(--fruit-purple) 30%);
  }
  .hero-visual .bowl {
    position: absolute; left: 124px; top: 4px; width: 364px; height: 364px;
    border-radius: 50%; border: 10px solid var(--bowl-rim);
    background: radial-gradient(circle, var(--bowl-cream) 0 40%, var(--bowl-oat) 100%);
    box-shadow: 0 6px 18px rgba(0,0,0,0.08);
  }
  .hero-visual .fruit-right {
    position: absolute; left: 436px; top: 212px; width: 136px; height: 143px; border-radius: 50%;
    background: radial-gradient(circle at 45% 50%, var(--fruit-yellow) 0 36%, var(--fruit-pink) 40%);
  }
  .rule--benefits { top: 964px; width: 450px; height: 1px; background: var(--orange-soft); }
  .rule--foot { top: 1086px; width: 450px; height: 1px; background: var(--orange-soft); }
  .benefit { position: absolute; top: 982px; width: 110px; transform: translateX(-50%); text-align: center; }
  .benefit svg { display: block; margin: 0 auto; width: 62px; height: 56px; }
  .benefit span { display: block; margin-top: 6px; font-size: 16px; font-weight: 500; color: var(--label-grey); white-space: nowrap; }
  .benefit--heart { left: 275px; }
  .benefit--eye { left: 403px; }
  .benefit--mobility { left: 516px; }
  .benefit--gut { left: 639px; }
  .net-weight { top: 1129px; font-size: 26px; font-weight: 500; color: var(--orange); }
</style>
</head>
<body>
  <main class="pack-front">
    <div class="centred brand">VitalRori</div>
    <div class="rule rule--top"></div>
    <h1 class="centred product-name">Instant Oatmeal</h1>
    <div class="rule rule--mid"></div>
    <p class="centred made-with">Made With</p>
    <p class="centred star-ingredient">Organic Passion Fruit</p>
    <p class="centred benefit-pill">Regulates Blood Glucose</p>

    <div class="hero-visual" role="img" aria-label="Bowl of creamy oatmeal with halved purple passion fruits and a green leaf">
      <div class="fruit-left"></div>
      <div class="fruit-right"></div>
      <div class="bowl"></div>
    </div>

    <div class="rule rule--benefits"></div>
    <div class="benefit benefit--heart">
      <svg viewBox="0 0 74 66" aria-hidden="true">
        <path d="M37 62 C10 42 4 30 4 20 C4 10 12 4 21 4 C28 4 33 8 37 14 C41 8 46 4 53 4 C62 4 70 10 70 20 C70 30 64 42 37 62Z" fill="var(--icon-grey)"/>
      </svg>
      <span>Heart Health</span>
    </div>
    <div class="benefit benefit--eye">
      <svg viewBox="0 0 74 66" aria-hidden="true">
        <path d="M2 33 C16 12 58 12 72 33 C58 54 16 54 2 33Z" fill="var(--icon-grey)"/>
        <circle cx="37" cy="33" r="15" fill="#fff"/>
        <circle cx="37" cy="33" r="9" fill="var(--icon-grey)"/>
      </svg>
      <span>Eyesight</span>
    </div>
    <div class="benefit benefit--mobility">
      <svg viewBox="0 0 74 66" aria-hidden="true" fill="none" stroke="var(--icon-grey)" stroke-width="5" stroke-linecap="round" stroke-linejoin="round">
        <path d="M10 48 C24 48 30 20 52 20"/>
        <path d="M44 12 L56 20 L46 30"/>
        <path d="M8 58 H40"/>
      </svg>
      <span>Mobility</span>
    </div>
    <div class="benefit benefit--gut">
      <svg viewBox="0 0 74 66" aria-hidden="true" fill="none" stroke="var(--icon-grey)" stroke-width="3" stroke-linecap="round" stroke-linejoin="round">
        <path d="M30 4 V16 C30 22 24 22 22 28 C18 38 26 44 34 42 C40 40 38 34 44 32 C54 30 60 38 56 48 C52 58 40 60 30 56 L22 62"/>
        <circle cx="46" cy="44" r="4"/>
      </svg>
      <span>Gut-Health</span>
    </div>
    <div class="rule rule--foot"></div>
    <p class="centred net-weight">Net weight: 450g</p>
  </main>
</body>
</html>
```